Ward Compass Business Card Design*

We need a business card design for our company Ward Compass. Our company is specialized in providing online consulting services regarding medical institutions, hospitals and doctors. We work with patients worldwide looking to choose between healthcare providers. We have a website you may use as a reference, where we list doctors and clinics worldwide. So we target Medical providers as well as patients worldwide.
Target Market(s)
Medical Providers and patients around the world
Industry/Entity Type
Medical
Contact Information for Business Card
Salwa Kettani
CEO
+90 612 348 2175
info@wardcompass.example
www.wardcompass.example
14 Annakhil 7 H.R.B. Rabat, Morocco
Requirements
Must have
- Company logo/name on one full side, personal info and smaller logo and company name on the other side.
Nice to have
- Smart and elegant design

```html
<!DOCTYPE html>
<html lang="en">
<head>
<meta charset="utf-8">
<title>Ward Compass — Business Card</title>
<link rel="stylesheet" href="https://fonts.googleapis.com/css2?family=Montserrat:wght@400;500;600&display=swap">
<style>
  :root {
    --page: #eceeef;
    --card-white: #ffffff;
    --brand-blue: #35a6d6;
    --brand-navy: #1d3f6b;
    --ink: #2a2a2a;
    --rule: #c9c9c9;
    --on-blue: #ffffff;
  }
  * { box-sizing: border-box; margin: 0; padding: 0; }
  html, body { width: 1200px; height: 1200px; overflow: hidden; }
  body {
    background: var(--page);
    font-family: "Montserrat", sans-serif;
    position: relative;
  }
  .card {
    position: absolute;
    border-radius: 17px;
    box-shadow: 4px 6px 10px rgba(0,0,0,0.22);
  }
  /* Back: personal details */
  .card-back {
    left: 136px; top: 315px; width: 327px; height: 570px;
    background: var(--card-white);
    text-align: center;
    color: var(--ink);
  }
  .back-mark {
    position: absolute; left: 0; right: 0; top: 150px;
    display: flex; flex-direction: column; align-items: center; gap: 14px;
  }
  .mark-dot {
    width: 64px; height: 64px; border-radius: 50%;
    background: var(--brand-navy);
  }
  .back-name {
    font-size: 17px; font-weight: 600; color: var(--brand-navy);
    letter-spacing: 0.5px;
  }
  .person {
    position: absolute; left: 0; right: 0; top: 355px;
  }
  .person-name {
    font-size: 23px; font-weight: 600; color: var(--brand-blue);
    line-height: 1.1;
  }
  .person-role {
    font-size: 13px; font-weight: 400; margin-top: 3px;
  }
  .icon-row {
    display: flex; align-items: center; justify-content: center;
    gap: 5px; margin: 9px 26px 0;
  }
  .icon-row .rule { flex: 1; height: 1px; background: var(--rule); }
  .icon-row svg { width: 18px; height: 18px; display: block; }
  .contact {
    font-size: 13.5px; line-height: 18px; margin-top: 6px;
  }
  .divider { height: 1px; background: var(--rule); margin: 8px 26px 10px; }
  .address { font-size: 13.5px; line-height: 19px; }

  /* Front: company name */
  .card-front {
    left: 493px; top: 558px; width: 571px; height: 327px;
    background: var(--brand-blue);
    display: flex; align-items: center; justify-content: center; gap: 22px;
  }
  .front-dot {
    width: 88px; height: 88px; border-radius: 50%;
    background: var(--on-blue);
  }
  .front-name {
    color: var(--on-blue);
    font-size: 36px; font-weight: 500;
    text-transform: uppercase; letter-spacing: 1.5px;
  }
</style>
</head>
<body>

<section class="card card-back" aria-label="Business card back">
  <div class="back-mark">
    <span class="mark-dot"></span>
    <span class="back-name">Ward Compass</span>
  </div>

  <div class="person">
    <p class="person-name">Salwa Kettani</p>
    <p class="person-role">CEO</p>

    <div class="icon-row">
      <span class="rule"></span>
      <svg viewBox="0 0 18 18" aria-label="Phone">
        <circle cx="9" cy="9" r="9" fill="var(--brand-blue)"/>
        <path d="M6 5.2c.6-.4 1.1-.3 1.4.2l.7 1.2c.2.4.1.8-.3 1.1l-.5.4c.4 1 1.2 1.8 2.2 2.3l.4-.5c.3-.4.7-.5 1.1-.3l1.2.7c.5.3.6.8.2 1.4-.6.8-1.6 1-2.6.5-1.8-.9-3.2-2.3-4-4.1-.4-.9-.4-1.9.2-2.4z" fill="#fff"/>
      </svg>
      <svg viewBox="0 0 18 18" aria-label="Email">
        <circle cx="9" cy="9" r="9" fill="var(--brand-blue)"/>
        <rect x="4.5" y="5.8" width="9" height="6.4" rx="0.8" fill="#fff"/>
        <path d="M4.8 6.2 9 9.4l4.2-3.2" fill="none" stroke="var(--brand-blue)" stroke-width="0.9"/>
      </svg>
      <svg viewBox="0 0 18 18" aria-label="Website">
        <circle cx="9" cy="9" r="9" fill="var(--brand-blue)"/>
        <g fill="none" stroke="#fff" stroke-width="0.9">
          <circle cx="9" cy="9" r="4.6"/>
          <ellipse cx="9" cy="9" rx="2" ry="4.6"/>
          <path d="M4.4 9h9.2M5 6.8h8M5 11.2h8"/>
        </g>
      </svg>
      <span class="rule"></span>
    </div>

    <div class="contact">
      <p>+90 612 348 2175</p>
      <p>info@wardcompass.example</p>
      <p>www.wardcompass.example</p>
    </div>
    <div class="divider"></div>
    <div class="address">
      <p>14 Annakhil 7 H.R.B.</p>
      <p>Rabat, Morocco</p>
    </div>
  </div>
</section>

<section class="card card-front" aria-label="Business card front">
  <span class="front-dot"></span>
  <span class="front-name">Ward Compass</span>
</section>

</body>
</html>
```